Computer consultant business card

Bexil Software is a newly started computer consulting company. It's a small one-man company that provides mostly Vornix applications but also websites in collaboration with designers. I'm running this company on the side of full time university studies.

I want the final design to be clean and memorable. Be creative! :)

Some inspiration:
http://www.pixelmarta.com/design/48317
http://www.pixelmarta.com/design/2739164/business-card-design-by-frostlynk
http://www.pixelmarta.com/design/604281/business-card-design-by-koralind-vestrabanu

See attachment for my company logo.
Updates

I would like to thank everyone for submitting! I'll need a couple of days to review and ultimately select a design.

Target Market(s)

Non-technical entrepreneurs and small companies.

Industry/Entity Type

University

Requirements
Must have
• My company logo.
In any way, both colors from my logo.
First- and last name, e-mail and phone number.
Double-sided design.
Nice to have
• Something creative with the symbol in my logo

```html
<!DOCTYPE html>
<html lang="en">
<head>
<meta charset="utf-8">
<title>Bexil Software – Business Card</title>
<link rel="stylesheet" href="https://fonts.googleapis.com/css2?family=Arimo:wght@400;700&display=swap">
<style>
  :root {
    --ink: #1f1f1f;
    --charcoal: #2a2828;
    --brand-blue: #4a74c4;
    --paper: #f7f7f7;
    --backdrop: #d9d6d2;
    --muted: #444444;
  }
  html, body {
    margin: 0;
    padding: 0;
    width: 1200px;
    height: 900px;
    overflow: hidden;
    background: var(--backdrop);
    font-family: "Arimo", Arial, sans-serif;
  }
  .canvas {
    width: 1200px;
    height: 900px;
    display: flex;
    flex-direction: column;
    align-items: center;
    justify-content: center;
    gap: 40px;
  }
  .card {
    position: relative;
    width: 700px;
    height: 400px;
    background: var(--paper);
    overflow: hidden;
    box-shadow: 0 6px 18px rgba(0,0,0,0.18);
  }
  .card-shape {
    position: absolute;
    inset: 0;
  }
  .front-url {
    position: absolute;
    top: 22px;
    left: 0;
    right: 0;
    text-align: center;
    font-size: 13px;
    color: var(--muted);
    letter-spacing: 0.5px;
  }
  .front-url .domain { color: var(--brand-blue); }
  .brand {
    position: absolute;
    top: 50%;
    left: 50%;
    transform: translate(-50%, -50%);
    display: flex;
    align-items: center;
    gap: 22px;
  }
  .brand-dot {
    width: 58px;
    height: 58px;
    border-radius: 50%;
    background: var(--brand-blue);
  }
  .brand-name {
    font-size: 86px;
    font-weight: 400;
    color: var(--charcoal);
    letter-spacing: 2px;
    line-height: 1;
  }
  .identity {
    position: absolute;
    top: 66px;
    left: 70px;
  }
  .person-name {
    margin: 0;
    font-size: 44px;
    font-weight: 700;
    color: var(--ink);
    letter-spacing: 1px;
  }
  .person-role {
    margin: 4px 0 0;
    font-size: 28px;
    font-weight: 400;
    color: var(--brand-blue);
  }
  .divider {
    position: absolute;
    top: 174px;
    left: 70px;
    width: 420px;
    height: 3px;
    background: var(--brand-blue);
  }
  .contacts {
    position: absolute;
    left: 80px;
    bottom: 46px;
    font-size: 14px;
    color: var(--ink);
    line-height: 1.7;
  }
  .contacts .row span { margin-right: 26px; }
  .contacts .label { color: var(--muted); margin-right: 6px; }
</style>
</head>
<body>
<main class="canvas">

  <section class="card card-front" aria-label="Card front">
    <svg class="card-shape" viewBox="0 0 700 400" aria-hidden="true">
      <rect width="700" height="400" fill="var(--charcoal)"/>
      <ellipse cx="350" cy="200" rx="430" ry="232" transform="rotate(-18 350 200)" fill="var(--brand-blue)"/>
      <ellipse cx="350" cy="200" rx="424" ry="226" transform="rotate(-18 350 200)" fill="var(--paper)"/>
    </svg>
    <div class="front-url">www.<span class="domain">marlofenn</span>.com</div>
    <div class="brand">
      <span class="brand-dot"></span>
      <span class="brand-name">bexil</span>
    </div>
  </section>

  <section class="card card-back" aria-label="Card back">
    <svg class="card-shape" viewBox="0 0 700 400" aria-hidden="true">
      <rect width="700" height="400" fill="var(--charcoal)"/>
      <ellipse cx="330" cy="230" rx="446" ry="276" transform="rotate(10 330 230)" fill="var(--brand-blue)"/>
      <ellipse cx="330" cy="230" rx="440" ry="270" transform="rotate(10 330 230)" fill="var(--paper)"/>
    </svg>
    <div class="identity">
      <h1 class="person-name">MARLO FENN</h1>
      <p class="person-role">Graphic Designer</p>
    </div>
    <div class="divider"></div>
    <div class="contacts">
      <div class="row">
        <span><span class="label">[ A ]</span>418 Ashgrove Ave, Tenby NY 60214</span>
        <span><span class="label">[ E ]</span>hello@marlofenn.com</span>
      </div>
      <div class="row">
        <span><span class="label">[ T ]</span>4821 7305</span>
        <span><span class="label">[ F ]</span>4821 7306</span>
      </div>
    </div>
  </section>

</main>
</body>
</html>
```